Kestal-Materials. Limestone; improving the world

New Limestone company and need logo design.
Limestone offsets carbon mitigation industries restore and replenish soil fertilities in the Prairies, the breadbasket of the world. At the same time, Limestone is proving a critical emergent component of carbon capture sequestration technology will therefore play a critical role in the development of the western Canadian energy industries
Our limestone resources are situated in the foothills of the Canadian Rockies well-positioned above the sprawling fields of the vast peace district.
Agriculture and oli sites
Kestal Materials
3 page

```html
<!DOCTYPE html>
<html lang="en">
<head>
<meta charset="utf-8">
<title>Kestal Materials</title>
<link rel="stylesheet" href="https://fonts.googleapis.com/css2?family=Montserrat:wght@500;600&family=Roboto:wght@400;500&display=swap">
<style>
:root{
  --green:#12d97b;
  --ink:#1a1a1a;
  --body:#7a7a7a;
  --band:#eeeeee;
  --blog-bg:#f4f4f4;
  --footer:#121212;
  --white:#ffffff;
}
*{margin:0;padding:0;box-sizing:border-box}
html,body{width:1200px;height:3505px;overflow:hidden;background:var(--white)}
body{position:relative;font-family:'Roboto',sans-serif;color:var(--ink)}
.abs{position:absolute}
.brand{font-family:'Montserrat',sans-serif;font-weight:500;font-size:28px;letter-spacing:.2px}
.btn{position:absolute;display:flex;align-items:center;justify-content:center;background:var(--green);color:var(--white);font-size:16px;font-weight:500;text-decoration:none}

/* header */
.site-header{position:absolute;left:0;top:0;width:1200px;height:80px;background:var(--white)}
.site-header .brand{position:absolute;left:87px;top:18px;color:var(--ink)}
.main-nav a{position:absolute;top:27px;font-size:16px;color:var(--ink);text-decoration:none}
.main-nav a.active{color:var(--green)}

/* hero */
.hero{position:absolute;left:0;top:80px;width:1200px;height:592px;
  background:radial-gradient(ellipse 220px 190px at 740px 390px,#cfe6d8 0%,#8fbf9c 45%,transparent 75%),
  linear-gradient(180deg,#6fa653 0%,#4e8a3a 35%,#3f7a2c 65%,#2c521c 100%)}
.hero-title{position:absolute;left:86px;top:88px;font-family:'Montserrat',sans-serif;font-weight:600;font-size:55px;color:var(--white)}
.hero-lead{position:absolute;left:89px;top:162px;width:720px;font-size:19.5px;line-height:27px;color:var(--white)}

/* shared */
.section-title{position:absolute;font-size:42px;font-weight:500;color:var(--ink)}
.copy{position:absolute;font-size:15.5px;line-height:28.6px;color:var(--body);text-align:justify}
.photo{position:absolute}
.frame{position:absolute;background:var(--green)}

.band{position:absolute;left:0;top:1216px;width:1200px;height:544px;background:var(--band)}
.blog-band{position:absolute;left:0;top:2521px;width:1200px;height:633px;background:var(--blog-bg)}

.post{position:absolute;top:2686px;width:335px}
.post .thumb{width:335px;height:224px}
.post h3{margin-top:12px;font-size:18px;line-height:21px;font-weight:500;color:var(--ink)}
.post time{display:block;margin-top:6px;font-size:14px;color:var(--ink)}
.post p{margin-top:8px;padding-left:2px;font-size:14.5px;line-height:21.5px;color:var(--body)}

/* footer */
.site-footer{position:absolute;left:0;top:3154px;width:1200px;height:351px;background:var(--footer);color:var(--white)}
.site-footer .brand{position:absolute;left:87px;top:76px}
.footer-about{position:absolute;left:89px;top:128px;width:380px;font-size:16px;line-height:26px}
.footer-col{position:absolute;top:72px}
.footer-col h4{font-family:'Montserrat',sans-serif;font-weight:500;font-size:27px;margin-bottom:12px}
.footer-col ul{list-style:none;padding-left:2px}
.footer-col li{font-size:16px;line-height:28px}
.social li{display:flex;align-items:center;gap:12px}
.social i{display:inline-block;width:13px;height:13px;background:var(--white);border-radius:2px}
.copyright{position:absolute;left:0;top:320px;width:1200px;text-align:center;font-size:12.5px}
</style>
</head>
<body>

<header class="site-header">
  <div class="brand">Kestal Materials</div>
  <nav class="main-nav">
    <a class="active" style="left:490px">Home</a>
    <a style="left:565px">About Us</a>
    <a style="left:664px">Services</a>
    <a style="left:758px">Blog</a>
    <a style="left:822px">Contact Us</a>
  </nav>
  <a class="btn" style="left:933px;top:19px;width:177px;height:42px">Customer Portal</a>
</header>

<section class="hero" role="img" aria-label="Glass globe resting in green grass among ferns">
  <h1 class="hero-title">Kestal Materials</h1>
  <p class="hero-lead">Lorem ipsum dolor sit amet, consectetur adipiscing elit, sed do eiusmod tempor incididunt ut labore et dolore magna aliqua.</p>
  <a class="btn" style="left:90px;top:238px;width:177px;height:42px">Customer Portal</a>
</section>

<section class="who">
  <h2 class="section-title" style="left:89px;top:758px">Who We Are</h2>
  <p class="copy" style="left:90px;top:834px;width:495px">Lorem ipsum dolor sit amet, consectetur adipiscing elit, sed do eiusmod tempor incididunt ut labore et dolore magna aliqua. Ut enim ad minim veniam, quis nostrud exercitation ullamco laboris nisi ut aliquip ex ea commodo consequat. Duis aute irure dolor in reprehenderit in voluptate velit esse cillum dolore eu fugiat nulla pariatur. Excepteur sint occæcat cupidatat non proident, sunt in culpa qui officia deserunt mollit anim id est laborum.</p>
  <a class="btn" style="left:90px;top:1070px;width:177px;height:42px">Read More</a>
  <div class="frame" style="left:626px;top:778px;width:494px;height:342px"></div>
  <div class="photo" role="img" aria-label="Close view of a cracked limestone rock face" style="left:616px;top:769px;width:494px;height:341px;background:linear-gradient(160deg,#e2d2b0 0%,#cdb88f 40%,#d9c8a2 70%,#bfa87c 100%)"></div>
</section>

<div class="band"></div>
<section class="mission">
  <h2 class="section-title" style="left:0;top:1307px;width:1200px;text-align:center">Mission</h2>
  <p class="copy" style="left:158px;top:1374px;width:884px;text-align:center;line-height:27.8px">Lorem ipsum dolor sit amet, consectetur adipiscing elit, sed do eiusmod tempor incididunt ut labore et dolore magna aliqua. Ut enim ad minim veniam, quis nostrud exercitation ullamco laboris nisi ut aliquip ex ea commodo consequat. Duis aute irure dolor in reprehenderit in voluptate velit esse cillum dolore eu fugiat nulla pariatur. Excepteur sint occæcat cupidatat non proident, sunt in culpa qui officia deserunt mollit anim id est laborum.</p>
  <div class="photo" role="img" aria-label="Video still of a hand holding a light bulb surrounded by green sustainability icons" style="left:166px;top:1517px;width:868px;height:457px;background:radial-gradient(ellipse 300px 220px at 434px 230px,#b9b96a 0%,#6f8a3a 45%,#2f5a26 80%,#22461c 100%)">
    <svg width="868" height="457" viewBox="0 0 868 457">
      <circle cx="434" cy="228" r="29" fill="none" stroke="#ffffff" stroke-width="3"/>
      <path d="M425 214 L449 228 L425 242 Z" fill="#ffffff"/>
    </svg>
  </div>
</section>

<section class="sustain">
  <div class="frame" style="left:79px;top:2082px;width:494px;height:342px"></div>
  <div class="photo" role="img" aria-label="Glass globe on dewy grass in soft sunlight" style="left:88px;top:2072px;width:494px;height:343px;background:radial-gradient(ellipse 90px 80px at 350px 190px,#e4eedc 0%,#a9c27a 60%,transparent 100%),linear-gradient(180deg,#d6dc9a 0%,#a9bd5c 45%,#6e9a34 75%,#4c7a22 100%)"></div>
  <h2 class="section-title" style="left:613px;top:2065px">Sustainability</h2>
  <p class="copy" style="left:614px;top:2137px;width:496px">Lorem ipsum dolor sit amet, consectetur adipiscing elit, sed do eiusmod tempor incididunt ut labore et dolore magna aliqua. Ut enim ad minim veniam, quis nostrud exercitation ullamco laboris nisi ut aliquip ex ea commodo consequat. Duis aute irure dolor in reprehenderit in voluptate velit esse cillum dolore eu fugiat nulla pariatur. Excepteur sint occæcat cupidatat non proident, sunt in culpa qui officia deserunt mollit anim id est laborum.</p>
  <a class="btn" style="left:615px;top:2373px;width:177px;height:42px">Read More</a>
</section>

<div class="blog-band"></div>
<section class="blog">
  <h2 class="section-title" style="left:0;top:2611px;width:1200px;text-align:center">Blog</h2>
  <article class="post" style="left:90px">
    <div class="thumb" role="img" aria-label="Many hands together holding a small seedling over a wooden table" style="background:linear-gradient(135deg,#8a5a34 0%,#3b4250 45%,#c7a27a 70%,#6a4a30 100%)"></div>
    <h3>Lorem ipsum dolor sit amet, consectetur adipiscing elit</h3>
    <time>10/05/2021</time>
    <p>Lorem ipsum dolor sit amet, consectetur adipiscing elit, sed do eiusmod tempor incididunt ut labore et dolore magna</p>
  </article>
  <article class="post" style="left:433px">
    <div class="thumb" role="img" aria-label="Pile of pale crushed limestone gravel" style="background:linear-gradient(135deg,#d8d2c8 0%,#bcb5aa 40%,#e2ddd4 70%,#a9a196 100%)"></div>
    <h3>Lorem ipsum dolor sit amet, consectetur adipiscing elit</h3>
    <time>10/05/2021</time>
    <p>Lorem ipsum dolor sit amet, consectetur adipiscing elit, sed do eiusmod tempor incididunt ut labore et dolore magna</p>
  </article>
  <article class="post" style="left:776px">
    <div class="thumb" role="img" aria-label="Young sprout in dark soil with glowing eco icons" style="background:radial-gradient(ellipse 140px 100px at 80px 60px,#c9cf88 0%,transparent 100%),linear-gradient(180deg,#5b6a2c 0%,#3a3a1c 60%,#2a1d12 100%)"></div>
    <h3>Lorem ipsum dolor sit amet, consectetur adipiscing elit</h3>
    <time>10/05/2021</time>
    <p>Lorem ipsum dolor sit amet, consectetur adipiscing elit, sed do eiusmod tempor incididunt ut labore et dolore magna</p>
  </article>
</section>

<footer class="site-footer">
  <div class="brand">Kestal Materials</div>
  <p class="footer-about">Lorem ipsum dolor sit amet, consectetur adipiscing elit, sed do eiusmod tempor incididunt ut labore et dolore magna aliqua.</p>
  <div class="footer-col" style="left:543px">
    <h4>Links</h4>
    <ul><li>Home</li><li>About Us</li><li>Services</li><li>Blog</li><li>Contact Us</li></ul>
  </div>
  <div class="footer-col" style="left:739px">
    <h4>Others</h4>
    <ul><li>FAQ</li><li>Privacy Policy</li><li>Terms &amp; Conditions</li></ul>
  </div>
  <div class="footer-col" style="left:977px">
    <h4>Follow Us</h4>
    <ul class="social">
      <li><i></i>Circlebook</li>
      <li><i></i>Snapgram</li>
      <li><i></i>Chirper</li>
      <li><i></i>Viewtube</li>
    </ul>
  </div>
  <p class="copyright">Copyrights © 2021, The Company Name. All rights reserved.</p>
</footer>

</body>
</html>
```